RWT Fittings Ltd Business Cards

We need a business card with our business logo. We provide window and door installations on high-rises in west coast British Colombia, Canada.

I would like my business information and details on one side of the card, and the other side the company name with logo

Target Market(s)

General Contractors

Industry/Entity Type

Construction

Contact Information for Business Card

one side i want my company name and logo in the dark theme logo that i provided

Requirements
Must have
• Marco Peltieri, 16045518293, RWTFittings@mailbox-demo.com, 1407-5194 Linden Row Burnaby BC, V5H 2K9, Owner & Manager

```html
<!DOCTYPE html>
<html lang="en">
<head>
<meta charset="utf-8">
<title>RWT Fittings Ltd Business Cards</title>
<link href="https://fonts.googleapis.com/css2?family=Roboto:wght@400;500;700&display=swap" rel="stylesheet">
<style>
  :root {
    --stage: #222223;
    --card: #1d1d21;
    --card-edge: #141417;
    --accent: #1ea0dc;
    --name-grey: #a3a5aa;
    --text-light: #e6e7ea;
    --emboss: #2c2c31;
    --emboss-hi: #3a3a40;
  }
  * { margin: 0; padding: 0; box-sizing: border-box; }
  html, body {
    width: 1200px; height: 780px; overflow: hidden;
    background: var(--stage);
    font-family: "Roboto", Arial, sans-serif;
  }
  .stage {
    position: relative; width: 1200px; height: 780px;
    display: flex; align-items: center; justify-content: center; gap: 40px;
  }
  .card {
    position: relative; width: 540px; height: 309px;
    background: var(--card);
    border-radius: 3px;
    box-shadow: 0 3px 0 var(--card-edge), 0 6px 0 #18181b, 0 24px 40px rgba(0,0,0,.55);
    overflow: hidden;
  }
  /* contact side */
  .contact { position: absolute; left: 34px; top: 38px; color: var(--text-light); }
  .contact-name {
    font-size: 30px; font-weight: 700; line-height: 1;
    padding-left: 14px; border-left: 4px solid var(--accent);
  }
  .contact-name .first { color: var(--accent); }
  .contact-name .last { color: var(--name-grey); }
  .contact-role { font-size: 14px; margin: 8px 0 18px 18px; }
  .contact-address { font-size: 14px; line-height: 1.45; margin-left: 18px; }
  .contact-lines { list-style: none; margin-top: 12px; font-size: 14px; line-height: 1.6; }
  .contact-lines li { display: flex; align-items: center; gap: 8px; }
  .contact-lines svg { width: 13px; height: 13px; fill: var(--accent); flex: none; }
  .wordmark-emboss {
    position: absolute; right: 28px; bottom: 28px;
    display: flex; align-items: center; gap: 12px;
    color: var(--emboss-hi); font-size: 34px; font-weight: 700; letter-spacing: 1px;
  }
  .wordmark-emboss .mark { width: 30px; height: 30px; background: var(--emboss); }
  /* logo side */
  .brand-side { display: flex; align-items: center; justify-content: center; }
  .wordmark {
    display: flex; align-items: center; gap: 14px;
    color: var(--text-light); font-size: 40px; font-weight: 700; letter-spacing: 1px;
  }
  .wordmark .mark { width: 34px; height: 34px; background: var(--accent); }
</style>
</head>
<body>
<main class="stage">
  <section class="card info-side">
    <div class="contact">
      <h1 class="contact-name"><span class="first">Marco</span> <span class="last">Peltieri</span></h1>
      <p class="contact-role">Owner &amp; Manager</p>
      <p class="contact-address">1407-5194 Linden Row<br>Burnaby BC, V5H 2K9</p>
      <ul class="contact-lines">
        <li>
          <svg viewBox="0 0 24 24" aria-hidden="true"><path d="M6.6 10.8a15.1 15.1 0 0 0 6.6 6.6l2.2-2.2c.3-.3.7-.4 1-.2 1.1.4 2.3.6 3.6.6.6 0 1 .4 1 1V20c0 .6-.4 1-1 1A17 17 0 0 1 3 4c0-.6.4-1 1-1h3.5c.6 0 1 .4 1 1 0 1.3.2 2.5.6 3.6.1.3 0 .7-.2 1z"/></svg>
          1 604 551 8293
        </li>
        <li>
          <svg viewBox="0 0 24 24" aria-hidden="true"><path d="M3 5h18v14H3zm2 2v.5l7 4.5 7-4.5V7zm0 2.9V17h14V9.9l-7 4.5z"/></svg>
          RWTFittings@mailbox-demo.com
        </li>
      </ul>
    </div>
    <div class="wordmark-emboss"><span class="mark"></span>RWT Fittings Ltd</div>
  </section>
  <section class="card brand-side">
    <div class="wordmark"><span class="mark"></span>RWT Fittings Ltd</div>
  </section>
</main>
</body>
</html>
```